Quillbay.vc needs a better website design!

We need a new and better website for Quillbay.vc. We're a Canadian venture capital firm that invests in innovative entrepreneurs. We compete against the following websites: tormelo.vc, brightvalefund.ca, kestrowvc.com, and dovaran.vc. We're a diverse group of partners and we're dedicated to the founders we invest in.
Updates

I don’t really like stock photos of random people as part of the website design…so please try to stay away from using those images. Thanks, Owen

Target Market(s)

Canadian entrepreneurs and investors

Industry/Entity Type

Venture capital, finance, investment, entrepreneurship

Coding

Coded - Design and coding required

Number of Pages Required

4 page

Font styles to use
Sans Serif

Colors

Designer to choose colors to be used in the design.

Requirements
Must have
• Clean crisp overall design. Fast and to the point.
Nice to have
• Check out www.quillbay.vc - I did it myself and it is too basic and too wordy.
Should not have
• No stock images with random people in them! Not too wordy or with too many large images that are slow to load.

```html
<!DOCTYPE html>
<html lang="en">
<head>
<meta charset="utf-8">
<title>Quillbay.vc — What We Look For</title>
<link href="https://fonts.googleapis.com/css2?family=Poppins:wght@400;500;600&display=swap" rel="stylesheet">
<style>
:root{
  --green:#7a9a2e;
  --ink:#1f2a1a;
  --text:#2b2b2b;
  --muted:#5c5c5c;
  --nav-active:#f1f1f1;
  --footer:#f5f5f5;
  --bar:#242424;
  --hero-a:#6f766f;
  --hero-b:#3f5a36;
  --hero-c:#24401f;
}
*{margin:0;padding:0;box-sizing:border-box}
html,body{width:817px;height:1200px;overflow:hidden;background:#fff}
body{font-family:'Poppins',sans-serif;color:var(--text);position:relative}
.header{position:absolute;left:0;top:0;width:817px;height:66px;background:#fff;z-index:3}
.brand{position:absolute;left:110px;top:20px;display:flex;align-items:center;gap:6px;font-weight:600;font-size:15px;color:var(--green)}
.brand-dot{width:18px;height:18px;border:2px solid var(--green);border-radius:50%}
.nav a{position:absolute;top:0;height:66px;line-height:68px;font-size:9.3px;color:#3a3a3a;text-decoration:none;white-space:nowrap}
.nav .active{background:var(--nav-active);color:var(--green);border-bottom:3px solid var(--green);height:69px;padding:0;width:97px;text-align:center}
.hero{position:absolute;left:0;top:66px;width:817px;height:215px;background:linear-gradient(100deg,var(--hero-b) 0%,var(--hero-a) 35%,var(--hero-a) 55%,var(--hero-c) 100%)}
.hero-title{position:absolute;left:163px;top:47px;width:490px;text-align:center;color:#fff;font-weight:600;font-size:15.5px;line-height:26px}
.wave{position:absolute;left:0;top:210px;width:817px;height:72px}
.breadcrumb{position:absolute;left:110px;top:253px;font-size:9.3px;color:#555}
.breadcrumb span{color:var(--green)}
.breadcrumb .sep{color:#777;margin:0 5px}
.page-title{position:absolute;left:0;width:817px;top:308px;text-align:center;font-weight:600;font-size:18.6px;color:var(--ink)}
.section-lead{position:absolute;left:110px;font-size:13.4px;color:var(--ink);white-space:nowrap}
.criteria{position:absolute;left:111px;height:41px;display:flex;align-items:center;gap:9px;font-size:9.3px;white-space:nowrap}
.criteria-icon{width:41px;height:41px;border:1px solid var(--green);border-radius:50%;display:flex;align-items:center;justify-content:center;flex:none}
.criteria b{font-weight:400;color:var(--text)}
.criteria em{font-style:normal;color:var(--muted)}
.divider{position:absolute;left:109px;top:539px;width:598px;border-top:1px dashed #ddd}
.footer{position:absolute;left:0;top:985px;width:817px;height:185px;background:var(--footer)}
.footer-brand{position:absolute;left:110px;top:64px;display:flex;align-items:center;gap:8px;font-weight:600;font-size:22px;color:var(--green)}
.footer-brand .brand-dot{width:30px;height:30px;border-width:3px}
.footer h3{position:absolute;font-weight:500;font-size:13.4px;color:var(--ink);white-space:nowrap}
.links{position:absolute;left:354px;top:64px;list-style:none;font-size:9.3px}
.links li{height:22px;color:#333;white-space:nowrap}
.links li::before{content:"›";margin-right:7px;color:#333}
.links li.current{color:var(--green)}
.links li.current::before{color:var(--green)}
.contact{position:absolute;left:580px;top:64px;font-size:9.3px;display:flex;align-items:center;gap:7px;color:#333}
.social{position:absolute;left:581px;top:121px;display:flex;gap:4px}
.social span{width:21px;height:21px;border-radius:50%}
.social .s1{background:#1fb5e6}
.social .s2{background:#1b86c0}
.copyright{position:absolute;left:0;top:1170px;width:817px;height:30px;background:var(--bar);color:#fff;font-size:9.3px;text-align:center;line-height:30px}
</style>
</head>
<body>
<header class="header">
  <div class="brand"><span class="brand-dot"></span>Quillbay.vc</div>
  <nav class="nav">
    <a style="left:406px">Home</a>
    <a style="left:470px">Team</a>
    <a style="left:534px">Companies</a>
    <a class="active" style="left:618px">What We Look For</a>
  </nav>
</header>

<section class="hero" role="img" aria-label="Misty green mountain range photograph">
  <p class="hero-title">Quillbay.vc is a venture capital firm that invests in innovative seed-stage technology companies in Western Canada focused on B2B and SaaS markets.</p>
</section>
<svg class="wave" viewBox="0 0 817 72" preserveAspectRatio="none">
  <path d="M0 46 C120 10 260 5 400 35 C520 62 650 80 817 42 L817 72 L0 72 Z" fill="#fff"/>
</svg>
<div class="breadcrumb">Home<span class="sep">»</span><span>What We Look For</span></div>

<h1 class="page-title">What We Look For</h1>
<h2 class="section-lead" style="top:345px;font-weight:400">We invest in innovative technology companies with these characteristics:</h2>

<div class="criteria" style="top:375px">
  <div class="criteria-icon"><svg width="20" height="20" viewBox="0 0 20 20" fill="none" stroke="#777" stroke-width="1"><circle cx="10" cy="4" r="2"/><circle cx="5" cy="13" r="2"/><circle cx="15" cy="13" r="2"/><path d="M10 6v4M6 11l3-1M14 11l-3-1"/><circle cx="10" cy="11" r="1.5" stroke="#7a9a2e"/></svg></div>
  <p><b>Founding Team:</b> <em>Visionary, Committed, Coachable, Skilled, Aligned, With Market Fit</em></p>
</div>
<div class="criteria" style="top:426px">
  <div class="criteria-icon"><svg width="20" height="20" viewBox="0 0 20 20" fill="none" stroke="#777" stroke-width="1"><circle cx="11" cy="9" r="6"/><path d="M6 13l-4 5"/><path d="M9 11V8M11 11V6M13 11V8"/><circle cx="15" cy="15" r="2" stroke="#7a9a2e"/></svg></div>
  <p><b>Total Addressable Market:</b> <em>Large, Growing, and Attractive; With a Manageable Competitive Landscape</em></p>
</div>
<div class="criteria" style="top:477px">
  <div class="criteria-icon"><svg width="20" height="20" viewBox="0 0 20 20" fill="none" stroke="#777" stroke-width="1"><path d="M3 18V14M6 18V12M9 18V10M12 18V8M15 18V6"/><circle cx="15" cy="4" r="2.5" stroke="#7a9a2e"/></svg></div>
  <p><b>Product Market Fit:</b> <em>MVP + Initial Market Validation; Early Revenue and Growth Potential</em></p>
</div>

<div class="divider"></div>
<h2 class="section-lead" style="top:556px;font-weight:400">Other things we consider in evaluating our venture capital investments:</h2>

<div class="criteria" style="top:586px">
  <div class="criteria-icon"><svg width="20" height="20" viewBox="0 0 20 20" fill="none" stroke="#777" stroke-width="1"><circle cx="10" cy="10" r="8"/><path d="M7 10l3 2 3-5" stroke="#7a9a2e"/></svg></div>
  <p><b>Timing:</b> <em>Supportive Market Trends; Not Too Early or Too Late, Just Right</em></p>
</div>
<div class="criteria" style="top:637px">
  <div class="criteria-icon"><svg width="20" height="20" viewBox="0 0 20 20" fill="none" stroke="#777" stroke-width="1"><path d="M10 2L19 18H1Z"/><path d="M10 7v6M10 15v1" stroke="#7a9a2e"/></svg></div>
  <p><b>Problem:</b> <em>Big Pain; Customers Care About It + Are Willing to Pay</em></p>
</div>
<div class="criteria" style="top:688px">
  <div class="criteria-icon"><svg width="20" height="20" viewBox="0 0 20 20" fill="none" stroke="#777" stroke-width="1"><circle cx="10" cy="7" r="4"/><path d="M3 19c0-5 14-5 14 0"/><path d="M8 15l2 2 2-2" stroke="#7a9a2e"/></svg></div>
  <p><b>Customers:</b> <em>Understand Who + How to Reach; Realistic Go to Market Strategy</em></p>
</div>
<div class="criteria" style="top:739px">
  <div class="criteria-icon"><svg width="20" height="20" viewBox="0 0 20 20" fill="none" stroke="#777" stroke-width="1"><rect x="8" y="2" width="4" height="3"/><path d="M10 5v4M4 9h12M4 9v4M10 9v4M16 9v4"/><circle cx="4" cy="15" r="2"/><circle cx="10" cy="15" r="2" stroke="#7a9a2e"/><circle cx="16" cy="15" r="2"/></svg></div>
  <p><b>Business Model:</b> <em>Clear + Compelling; Increasing Scale Returns; Realizable Projections</em></p>
</div>
<div class="criteria" style="top:791px">
  <div class="criteria-icon"><svg width="20" height="20" viewBox="0 0 20 20" fill="none" stroke="#777" stroke-width="1"><path d="M4 8v6l3 4M16 8v6l-3 4"/><path d="M10 2v10M7 4v6M13 4v6" stroke="#7a9a2e"/></svg></div>
  <p><b>Competitive Advantage:</b> <em>Secret Sauce / Protective Moat for Product or Technology</em></p>
</div>
<div class="criteria" style="top:842px">
  <div class="criteria-icon"><svg width="20" height="20" viewBox="0 0 20 20" fill="none" stroke="#777" stroke-width="1"><circle cx="12" cy="6" r="4" stroke="#7a9a2e"/><path d="M2 14h4l4 1h5l3-3M2 18h6l8-2"/></svg></div>
  <p><b>Funding:</b> <em>Smart Use; Enough to Reach Milestones; Series A Potential; Exit Opportunities</em></p>
</div>
<div class="criteria" style="top:893px">
  <div class="criteria-icon"><svg width="20" height="20" viewBox="0 0 20 20" fill="none" stroke="#777" stroke-width="1"><path d="M4 2h9l3 3v13H4Z"/><path d="M7 7h6M7 10h6"/><path d="M6 15l3-2 2 1 3-2" stroke="#7a9a2e"/></svg></div>
  <p><b>Deal Terms:</b> <em>Valuation, Investment Amount, % Ownership; Cap Table; USA Terms</em></p>
</div>

<footer class="footer">
  <div class="footer-brand"><span class="brand-dot"></span>Quillbay.vc</div>
  <h3 style="left:354px;top:37px">Quick Links</h3>
  <ul class="links" style="top:63px">
    <li>Home</li><li>Team</li><li>Companies</li><li class="current">What We Look For</li>
  </ul>
  <h3 style="left:580px;top:38px">Get In Touch</h3>
  <div class="contact" style="top:64px"><svg width="10" height="8" viewBox="0 0 10 8"><rect width="10" height="8" fill="#7a9a2e"/><path d="M0 0l5 4 5-4" stroke="#fff" fill="none"/></svg>info@quillbay.vc</div>
  <h3 style="left:580px;top:96px">Follow Us</h3>
  <div class="social"><span class="s1"></span><span class="s2"></span></div>
</footer>
<div class="copyright">Copyright © 2021 Quillbay.vc - All Rights Reserved.</div>
</body>
</html>
```